Harlow Mechanical Contractors needs a Website

Create basic website for commercial plumbing and mechanical contractor; to include pictures of works in progress and completed works, description of all services offered and geographical locations and licenses

Target Market(s)

General Contractors, Real Estate Developers, Construction Companies

Industry/Entity Type

Construction

Coding

Coded - Design and coding required

Number of Pages Required

5+ page

• See logo attached to project

Colors
0392cd

```html
<!DOCTYPE html>
<html lang="en">
<head>
<meta charset="utf-8">
<title>Harlow Mechanical Contractors</title>
<link href="https://fonts.googleapis.com/css2?family=Arimo:wght@400;700&family=Open+Sans:wght@400;600;700&display=swap" rel="stylesheet">
<style>
:root{
  --blue:#0392cd;
  --blue-dark:#0a6fa8;
  --nav:#1187c9;
  --ink:#1f1f1f;
  --text:#6b6b6b;
  --line:#dcdcdc;
  --grey-bg:#f1f1f1;
  --footer:#161616;
  --white:#ffffff;
}
*{box-sizing:border-box;margin:0;padding:0}
html,body{width:1200px;height:2647px;overflow:hidden;background:var(--white)}
body{position:relative;font-family:"Open Sans",Arial,sans-serif;color:var(--text)}
.abs{position:absolute}
h1,h2,h3{font-family:"Arimo",Arial,sans-serif;color:var(--ink);font-weight:700}
a{color:inherit;text-decoration:none}

/* header */
.topline{left:0;top:0;width:1200px;height:5px;background:var(--blue)}
.brand{left:92px;top:18px;display:flex;align-items:center;gap:12px;font-family:"Arimo",Arial,sans-serif;font-weight:700;font-size:17px;line-height:18px;color:var(--ink);z-index:3}
.brand-dot{width:72px;height:72px;border-radius:50%;background:var(--blue);border:5px solid var(--white);box-shadow:0 0 0 1px var(--line)}
.contact-chip{top:22px;display:flex;gap:14px;align-items:flex-start}
.chip-icon{width:28px;height:28px;border-radius:50%;border:2px solid var(--blue);display:flex;align-items:center;justify-content:center}
.chip-label{font-size:12px;font-weight:700;color:var(--ink);line-height:16px}
.chip-phone{font-size:19px;font-weight:700;color:var(--blue);line-height:22px}
.chip-mail{font-size:13px;color:var(--blue);line-height:20px}
.estimate{left:928px;top:20px;width:172px;height:42px;background:var(--blue);color:var(--white);font-weight:700;font-size:13px;display:flex;align-items:center;justify-content:center;border-radius:3px;box-shadow:0 2px 0 var(--blue-dark)}
.navbar{left:0;top:81px;width:1200px;height:44px;background:var(--nav)}
.nav-item{top:81px;height:44px;line-height:44px;color:var(--white);font-family:"Arimo",Arial,sans-serif;font-weight:700;font-size:15px}
.nav-item.active{color:#0d3f73}

/* hero */
.hero{left:0;top:125px;width:1200px;height:408px;background:linear-gradient(180deg,#5c6a74 0%,#8e9aa2 35%,#6f7c84 65%,#3e4a52 100%)}
.hero-title{left:0;top:240px;width:1200px;text-align:center;color:var(--white);font-size:54px;text-shadow:0 2px 4px rgba(0,0,0,.5)}
.hero-sub{left:0;top:306px;width:1200px;text-align:center;color:var(--white);font-size:25px;text-shadow:0 2px 4px rgba(0,0,0,.5)}
.hero-btn{left:516px;top:360px;width:169px;height:44px;background:var(--blue);color:var(--white);font-family:"Arimo",Arial,sans-serif;font-weight:700;font-size:15px;display:flex;align-items:center;justify-content:center;border-radius:2px}
.hero-arrow{top:307px;width:44px;height:44px;border-radius:50%;background:rgba(0,0,0,.35);display:flex;align-items:center;justify-content:center}

/* welcome */
.section-title{left:0;width:1200px;text-align:center;font-size:33px}
.welcome-copy{left:170px;top:625px;width:860px;text-align:center;font-size:12px;line-height:23px}
.feature{top:708px;width:233px;height:250px;border:2px solid var(--line);background:var(--white);text-align:center;padding-top:18px}
.feature-icon{width:102px;height:102px;border-radius:50%;background:var(--blue);margin:0 auto;display:flex;align-items:center;justify-content:center}
.feature h3{font-size:15px;margin-top:22px;letter-spacing:.3px}
.feature p{font-size:12px;line-height:22px;margin:6px 14px 0}
.more{font-family:"Arimo",Arial,sans-serif;font-weight:700;font-size:12px;color:var(--blue)}
.feature .more{display:block;margin-top:8px}

/* services */
.services{left:0;top:1015px;width:1200px;height:506px;background:linear-gradient(135deg,#0c6ea8 0%,#1b8fcc 45%,#0d6aa2 100%)}
.services .section-title{color:var(--white)}
.service{top:1142px;width:312px}
.service-photo{width:312px;height:189px;border:3px solid var(--white)}
.service h3{color:var(--white);font-size:22px;margin-top:14px}
.service p{color:#e3f2fb;font-size:12px;line-height:21px;margin-top:6px}
.service .more{color:var(--white);display:block;margin-top:14px}

/* why & news */
.col-title{font-size:33px}
.why-copy{left:100px;top:1632px;width:450px;font-size:12px;line-height:21px}
.why-list{left:100px;top:1708px;width:460px;list-style:none}
.why-list li{display:flex;align-items:center;gap:14px;height:37px;font-size:12px}
.tick{width:15px;height:15px;border-radius:50%;background:var(--blue);display:flex;align-items:center;justify-content:center;flex:none}
.news{left:588px;width:514px;display:flex;gap:21px}
.news-photo{width:153px;height:117px;flex:none}
.news h4{font-family:"Open Sans",Arial,sans-serif;font-weight:700;font-size:13px;line-height:21px;color:var(--ink);text-decoration:underline;text-transform:uppercase}
.news-meta{display:flex;gap:16px;font-size:11px;font-style:italic;color:var(--blue);margin-top:5px}
.news p{font-size:12px;line-height:21px;margin-top:6px}
.news-rule{left:588px;top:1770px;width:514px;height:1px;background:var(--line)}

/* projects */
.projects{left:0;top:2013px;width:1200px;height:331px;background:var(--grey-bg)}
.project{top:2112px;width:242px;height:177px}
.slider-arrow{top:2176px;width:46px;height:46px;border-radius:50%;background:#c9c9c9;display:flex;align-items:center;justify-content:center}

/* footer */
.footer{left:0;top:2344px;width:1200px;height:303px;background:var(--footer)}
.footer-line{left:0;top:2344px;width:1200px;height:5px;background:var(--blue)}
.footer-brand{left:94px;top:2430px;display:flex;align-items:center;gap:14px;color:var(--white);font-family:"Arimo",Arial,sans-serif;font-weight:700;font-size:20px;line-height:22px}
.footer-dot{width:60px;height:60px;border-radius:50%;background:var(--white)}
.footer-rule{top:2372px;width:1px;height:180px;background:#333}
.footer h3{color:var(--white);font-size:17px}
.footer-links{list-style:none;color:#d6d6d6;font-size:12px;line-height:18px}
.footer-copy{color:#d6d6d6;font-size:12px;line-height:21px}
.field{width:232px;height:34px;background:var(--white);color:#777;font-size:12px;padding-left:14px;line-height:34px}
.subscribe{width:100px;height:36px;border:2px solid var(--white);color:var(--white);font-weight:700;font-size:12px;display:flex;align-items:center;justify-content:center;border-radius:3px}
.contact-row{display:flex;gap:18px;color:#d6d6d6;font-size:12px;line-height:16px}
.contact-row svg{flex:none;margin-top:1px}
.legal{left:100px;top:2602px;color:#d6d6d6;font-size:12px}
.social{top:2592px;width:34px;height:34px;border-radius:50%;border:2px solid var(--white)}
.foot-rule2{left:94px;top:2576px;width:1010px;height:1px;background:#2c2c2c}
</style>
</head>
<body>

<!-- header -->
<div class="abs topline"></div>
<div class="abs navbar"></div>
<div class="abs brand"><span class="brand-dot"></span><span>HARLOW<br>MECHANICAL<br>CONTRACTORS</span></div>

<div class="abs contact-chip" style="left:410px">
  <span class="chip-icon"><svg width="14" height="14" viewBox="0 0 24 24"><path fill="#0392cd" d="M6.6 10.8a15.1 15.1 0 0 0 6.6 6.6l2.2-2.2c.3-.3.7-.4 1-.2 1.1.4 2.3.6 3.6.6.6 0 1 .4 1 1V20c0 .6-.4 1-1 1A17 17 0 0 1 3 4c0-.6.4-1 1-1h3.5c.6 0 1 .4 1 1 0 1.3.2 2.5.6 3.6.1.3 0 .7-.2 1z"/></svg></span>
  <div><div class="chip-label">CALL US ON :</div><div class="chip-phone">1-800-555-0142</div></div>
</div>
<div class="abs contact-chip" style="left:606px">
  <span class="chip-icon"><svg width="14" height="14" viewBox="0 0 24 24"><path fill="#0392cd" d="M3 5h18v14H3z"/><path fill="none" stroke="#fff" stroke-width="2" d="M3 6l9 7 9-7"/></svg></span>
  <div><div class="chip-label">EMAIL US ON :</div><div class="chip-mail">info@harlowmechanicalco.com</div></div>
</div>
<a class="abs estimate">GET A FREE ESTIMATE</a>

<a class="abs nav-item active" style="left:236px">HOME</a>
<a class="abs nav-item" style="left:318px">ABOUT US</a>
<a class="abs nav-item" style="left:431px">SERVICES</a>
<a class="abs nav-item" style="left:540px">PROJECTS</a>
<a class="abs nav-item" style="left:653px">PORTFOLIO</a>
<a class="abs nav-item" style="left:776px">BLOG</a>
<a class="abs nav-item" style="left:852px">CAREERS</a>
<a class="abs nav-item" style="left:960px">CONTACT US</a>
<span class="abs" style="left:1092px;top:95px"><svg width="16" height="16" viewBox="0 0 24 24"><circle cx="10" cy="10" r="6.5" fill="none" stroke="#fff" stroke-width="3"/><path d="M15 15l6 6" stroke="#fff" stroke-width="3.5"/></svg></span>

<!-- hero -->
<div class="abs hero" role="img" aria-label="Mechanical plant room with insulated steel pipework, valves and pumps"></div>
<h1 class="abs hero-title">Harlow Mechanical Contractors</h1>
<p class="abs hero-sub">We are a commercial plumbing and mechanical contractor</p>
<a class="abs hero-btn">FIND OUT MORE</a>
<span class="abs hero-arrow" style="left:54px"><svg width="14" height="18" viewBox="0 0 14 18"><path d="M10 2L3 9l7 7" fill="none" stroke="#fff" stroke-width="3"/></svg></span>
<span class="abs hero-arrow" style="left:1102px"><svg width="14" height="18" viewBox="0 0 14 18"><path d="M4 2l7 7-7 7" fill="none" stroke="#fff" stroke-width="3"/></svg></span>

<!-- welcome -->
<h2 class="abs section-title" style="top:574px">Welcome to Harlow Mechanical Contractors</h2>
<p class="abs welcome-copy">At vero eos et accusamus et iusto odio dignissimos ducimus qui blanditiis praesentium voluptatum deleniti atque corrupti quos dolores et quas mole stias excepturi sint m deleoccaecati cupiditate non provident, similique sunt in culpa qui officia deserunt mollitia animi, id est</p>

<div class="abs feature" style="left:97px">
  <div class="feature-icon"><svg width="50" height="50" viewBox="0 0 24 24"><path fill="#fff" d="M2 10h4v11H2zM8 20V10l5-7c1.2 0 2 .9 1.8 2L14 9h6c1.1 0 2 .9 1.8 2l-1.6 8c-.2.6-.7 1-1.3 1z"/></svg></div>
  <h3>QUALITY PLUMBING</h3><p>At vero eos et accusamus et iusto od io dignissimos ducimus qui</p><a class="more">READ MORE &gt;&gt;</a>
</div>
<div class="abs feature" style="left:355px">
  <div class="feature-icon"><svg width="50" height="50" viewBox="0 0 24 24"><rect x="2" y="7" width="20" height="14" rx="2" fill="#fff"/><path d="M8 7V4h8v3" fill="none" stroke="#fff" stroke-width="2"/><path d="M8 7v14M16 7v14" stroke="#0392cd" stroke-width="1.5"/></svg></div>
  <h3>PROFESSIONALISM</h3><p>At vero eos et accusamus et iusto od io dignissimos ducimus qui</p><a class="more">READ MORE &gt;&gt;</a>
</div>
<div class="abs feature" style="left:611px">
  <div class="feature-icon"><svg width="48" height="50" viewBox="0 0 24 24"><path fill="#fff" d="M3 2h18v10c0 5-4 8.5-9 10-5-1.5-9-5-9-10z"/><path fill="#0392cd" d="M8 6h8v6c0 2.5-1.8 4.3-4 5.2-2.2-.9-4-2.7-4-5.2z"/></svg></div>
  <h3>RELIABILITY</h3><p>At vero eos et accusamus et iusto od io dignissimos ducimus qui</p><a class="more">READ MORE &gt;&gt;</a>
</div>
<div class="abs feature" style="left:868px">
  <div class="feature-icon"><svg width="54" height="54" viewBox="0 0 24 24"><circle cx="9" cy="14" r="5" fill="none" stroke="#fff" stroke-width="3" stroke-dasharray="2 1.2"/><circle cx="9" cy="14" r="2.2" fill="#fff"/><circle cx="17" cy="6.5" r="3.4" fill="none" stroke="#fff" stroke-width="2.4" stroke-dasharray="1.5 1"/><circle cx="17" cy="6.5" r="1.3" fill="#fff"/></svg></div>
  <h3>EFFICIENCY</h3><p>At vero eos et accusamus et iusto od io dignissimos ducimus qui</p><a class="more">READ MORE &gt;&gt;</a>
</div>

<!-- services -->
<div class="abs services"></div>
<h2 class="abs section-title" style="top:1071px;color:#fff">We Install Full Plumbing Services for the Following</h2>
<div class="abs service" style="left:97px">
  <div class="service-photo" role="img" aria-label="Bright open-plan office with white desks and black chairs" style="background:linear-gradient(180deg,#e9ecee,#b9bec2)"></div>
  <h3>Large Offices</h3><p>Nam libero tempore, cum soluta nobis est eligendi opti ocumque nihil impedit quo minus id quod maxime pla ceat facere possimus, omnis volup.</p><a class="more">READ MORE &gt;&gt;</a>
</div>
<div class="abs service" style="left:443px">
  <div class="service-photo" role="img" aria-label="Modern condominium building with balconies under a blue sky" style="background:linear-gradient(180deg,#6fa7de 0%,#d8dde0 55%,#6d9a45 100%)"></div>
  <h3>Condominiums</h3><p>Nam libero tempore, cum soluta nobis est eligendi opti ocumque nihil impedit quo minus id quod maxime pla ceat facere possimus, omnis volup.</p><a class="more">READ MORE &gt;&gt;</a>
</div>
<div class="abs service" style="left:789px">
  <div class="service-photo" role="img" aria-label="Large industrial hall with production machinery" style="background:linear-gradient(180deg,#46606e,#8a9a7a 70%,#6b6f63)"></div>
  <h3>Industrial Projects</h3><p>Nam libero tempore, cum soluta nobis est eligendi opti ocumque nihil impedit quo minus id quod maxime pla ceat facere possimus, omnis volup.</p><a class="more">READ MORE &gt;&gt;</a>
</div>

<!-- why choose us -->
<h2 class="abs col-title" style="left:100px;top:1570px">Why Choose Us</h2>
<p class="abs why-copy">Temporibus autem quibusdam et aut officiis debitis aut rerum necessitatibus saepe eveniet ut et voluptates repudiandae sint et molestiae non recusandae. Itaque earum rerum hic tenetur a sapiente delectus</p>
<ul class="abs why-list">
  <li><span class="tick"><svg width="9" height="9" viewBox="0 0 10 10"><path d="M1.5 5l2.5 2.5 4.5-5" fill="none" stroke="#fff" stroke-width="1.8"/></svg></span>Blanditiis praesentium voluptatum deleniti atque corrupti quos</li>
  <li><span class="tick"><svg width="9" height="9" viewBox="0 0 10 10"><path d="M1.5 5l2.5 2.5 4.5-5" fill="none" stroke="#fff" stroke-width="1.8"/></svg></span>Sed ut perspiciatis unde omnis iste natus error sit voluptatem accusanti</li>
  <li><span class="tick"><svg width="9" height="9" viewBox="0 0 10 10"><path d="M1.5 5l2.5 2.5 4.5-5" fill="none" stroke="#fff" stroke-width="1.8"/></svg></span>But I must explain to you how all this mistaken idea of denouncing</li>
  <li><span class="tick"><svg width="9" height="9" viewBox="0 0 10 10"><path d="M1.5 5l2.5 2.5 4.5-5" fill="none" stroke="#fff" stroke-width="1.8"/></svg></span>Nemo enim ipsam voluptatem quia voluptas sit aspernatur</li>
  <li><span class="tick"><svg width="9" height="9" viewBox="0 0 10 10"><path d="M1.5 5l2.5 2.5 4.5-5" fill="none" stroke="#fff" stroke-width="1.8"/></svg></span>At vero eos et accusamus et iusto odio dignissimos ducimus qui</li>
  <li><span class="tick"><svg width="9" height="9" viewBox="0 0 10 10"><path d="M1.5 5l2.5 2.5 4.5-5" fill="none" stroke="#fff" stroke-width="1.8"/></svg></span>Nam libero tempore, cum soluta nobis est eligendi optio cumque nihil</li>
</ul>
<a class="abs more" style="left:100px;top:1942px">READ MORE &gt;&gt;</a>

<!-- news -->
<h2 class="abs col-title" style="left:588px;top:1570px">Our News</h2>
<article class="abs news" style="top:1634px">
  <div class="news-photo" role="img" aria-label="Plumber in blue overalls working on a wall-mounted installation" style="background:linear-gradient(135deg,#2f5f9c,#c9c2b4)"></div>
  <div><h4>At vero eos et accusamus et iusto odiodig nissimos ducimus qui bland</h4>
  <div class="news-meta"><span>15/10/2015</span><span>John Doe</span><span>4 Comments</span></div>
  <p>Duis aute irure dolor in reprehenderit in voluptate velit esse cillum dolore eu fugiat nulla pariatur.</p></div>
</article>
<div class="abs news-rule"></div>
<article class="abs news" style="top:1789px">
  <div class="news-photo" role="img" aria-label="Technician adjusting valves and gauges on industrial piping" style="background:linear-gradient(135deg,#5a6d7c,#b4402e 60%,#8f9aa3)"></div>
  <div><h4>At vero eos et accusamus et iusto odiodig nissimos ducimus qui bland</h4>
  <div class="news-meta"><span>15/10/2015</span><span>John Doe</span><span>4 Comments</span></div>
  <p>Duis aute irure dolor in reprehenderit in voluptate velit esse cillum dolore eu fugiat nulla pariatur.</p></div>
</article>
<div class="abs news-rule" style="top:1925px"></div>
<a class="abs more" style="left:588px;top:1942px">VIEW MORE &gt;&gt;</a>

<!-- projects -->
<div class="abs projects"></div>
<h2 class="abs section-title" style="top:2053px">Our Projects</h2>
<div class="abs project" style="left:99px;background:linear-gradient(135deg,#6a4a2e,#c48a4c 50%,#3f4c5c)" role="img" aria-label="Close-up of copper and steel ductwork under warm light"></div>
<div class="abs project" style="left:351px;background:linear-gradient(180deg,#e6e0d6,#b8aa92 60%,#6d5a44)" role="img" aria-label="Finished kitchen with marble island and pendant lights"></div>
<div class="abs project" style="left:605px;background:linear-gradient(180deg,#2f79c6 0%,#9c7650 55%,#5a7a3a 100%)" role="img" aria-label="Completed mid-rise apartment building"></div>
<div class="abs project" style="left:858px;background:linear-gradient(180deg,#dfe6ec,#9fb0c4 60%,#5d86b8)" role="img" aria-label="Finished open-plan office interior"></div>
<span class="abs slider-arrow" style="left:51px"><svg width="12" height="18" viewBox="0 0 12 18"><path d="M9 2L2 9l7 7" fill="none" stroke="#fff" stroke-width="2.5"/></svg></span>
<span class="abs slider-arrow" style="left:1101px"><svg width="12" height="18" viewBox="0 0 12 18"><path d="M3 2l7 7-7 7" fill="none" stroke="#fff" stroke-width="2.5"/></svg></span>

<!-- footer -->
<footer>
<div class="abs footer"></div>
<div class="abs footer-line"></div>
<div class="abs footer-brand"><span class="footer-dot"></span><span>HARLOW<br>MECHANICAL<br>CONTRACTORS</span></div>

<div class="abs footer-rule" style="left:385px"></div>
<div class="abs footer-rule" style="left:565px"></div>
<div class="abs footer-rule" style="left:838px"></div>

<div class="abs" style="left:402px;top:2375px">
  <h3>INFORMATION</h3>
  <ul class="footer-links" style="margin-top:18px">
    <li>Home</li><li>About us</li><li>Services</li><li>Projects</li><li>Portfolio</li><li>Blog</li><li>Careers</li><li>Contact Us</li>
  </ul>
</div>
<div class="abs" style="left:584px;top:2375px">
  <h3>NEWSLETTER</h3>
  <p class="footer-copy" style="margin-top:16px;width:230px">Register your email address to get information about us</p>
  <div class="field" style="margin-top:12px">Email Address</div>
  <div class="subscribe" style="margin-top:13px">SUBSCRIBE</div>
</div>
<div class="abs" style="left:863px;top:2375px">
  <h3>CONTACT US</h3>
  <div class="contact-row" style="margin-top:18px"><svg width="12" height="14" viewBox="0 0 24 24"><path fill="#fff" d="M12 2a7 7 0 0 0-7 7c0 5 7 13 7 13s7-8 7-13a7 7 0 0 0-7-7zm0 9.5A2.5 2.5 0 1 1 12 6.5a2.5 2.5 0 0 1 0 5z"/></svg><span>218 Larkspur Avenue, Suite 410<br>Easton, New York 10245</span></div>
  <div class="contact-row" style="margin-top:16px"><svg width="12" height="12" viewBox="0 0 24 24"><path fill="#fff" d="M6.6 10.8a15.1 15.1 0 0 0 6.6 6.6l2.2-2.2c.3-.3.7-.4 1-.2 1.1.4 2.3.6 3.6.6.6 0 1 .4 1 1V20c0 .6-.4 1-1 1A17 17 0 0 1 3 4c0-.6.4-1 1-1h3.5c.6 0 1 .4 1 1 0 1.3.2 2.5.6 3.6.1.3 0 .7-.2 1z"/></svg><span>1 800 555 0142</span></div>
  <div class="contact-row" style="margin-top:16px"><svg width="12" height="12" viewBox="0 0 24 24"><rect x="3" y="8" width="18" height="13" fill="#fff"/><rect x="7" y="3" width="10" height="6" fill="none" stroke="#fff" stroke-width="2"/></svg><span>1 800 555 0178</span></div>
  <div class="contact-row" style="margin-top:16px"><svg width="12" height="12" viewBox="0 0 24 24"><path fill="#fff" d="M2 5h20v14H2z"/><path fill="none" stroke="#161616" stroke-width="2" d="M2 6l10 7 10-7"/></svg><span>info@harlowmechanicalco.com</span></div>
</div>

<div class="abs foot-rule2"></div>
<p class="abs legal">Copyrights © 2016 ,Harlow Mechanical Contractors. All rights reserved.</p>
<span class="abs social" style="left:948px"></span>
<span class="abs social" style="left:988px"></span>
<span class="abs social" style="left:1028px"></span>
<span class="abs social" style="left:1068px"></span>
</footer>

</body>
</html>
```